Business cards to launch an education platform

Hi,
I am looking at having new business cards designed.
I am a startup, developing a web platform for schools and university, the education world. It's an online assessment system.
I would like a card that looks classy, and that is using the colors and the font of my logo.

I have attached:
1) my logo
2) A business card that I have designed quickly so you can have all the information required in the card, but I really don't like it.
3) The font that I am using (Lato Regular) to design my web platform
4) Some screenshots of my web platform so you can have a look at the style that I have.

Target Market(s)

Major market: Education system: Schools and university
Minor markets: Business in general

Industry/Entity Type

Business

Contact Information for Business Card

Clara Fenwick
Director

M: 0437 518 902
E: clara.fenwick@amberLoomSystems.com.au

Requirements
Must have
• The colors of my logo

```html
<!DOCTYPE html>
<html lang="en">
<head>
<meta charset="utf-8">
<title>Amber Loom Systems – Business Cards</title>
<link rel="stylesheet" href="https://fonts.googleapis.com/css2?family=Lato:wght@300;400;700&display=swap">
<style>
  :root {
    --page-bg: #e9ebee;
    --card-white: #ffffff;
    --blue-deep: #0b3f86;
    --blue-mid: #1560b3;
    --blue-bright: #1f86d6;
    --blue-light: #3fb2ea;
    --blue-pale: #7fd0f5;
    --text-white: #ffffff;
    --text-soft: #d6e8f8;
    --shadow: rgba(10, 30, 60, 0.22);
  }
  * { margin: 0; padding: 0; box-sizing: border-box; }
  html, body {
    width: 1200px;
    height: 950px;
    overflow: hidden;
    background: var(--page-bg);
    font-family: "Lato", sans-serif;
  }
  .sheet {
    width: 1200px;
    height: 950px;
    display: flex;
    flex-direction: column;
    align-items: center;
    justify-content: center;
    gap: 50px;
  }
  .card {
    position: relative;
    width: 700px;
    height: 400px;
    border-radius: 4px;
    overflow: hidden;
    box-shadow: 0 10px 28px var(--shadow);
  }
  .card-art {
    position: absolute;
    inset: 0;
    width: 100%;
    height: 100%;
  }

  /* Front */
  .brand-front {
    position: absolute;
    left: 62px;
    top: 96px;
    display: flex;
    align-items: center;
    gap: 18px;
  }
  .brand-mark {
    width: 62px;
    height: 62px;
    background: var(--blue-mid);
  }
  .brand-name {
    color: var(--blue-mid);
    font-weight: 400;
    font-size: 34px;
    letter-spacing: 3px;
    line-height: 1.05;
    text-transform: uppercase;
  }
  .contact {
    position: absolute;
    left: 318px;
    top: 290px;
    color: var(--text-white);
  }
  .contact-name {
    font-size: 19px;
    font-weight: 700;
    letter-spacing: 0.5px;
    text-transform: uppercase;
  }
  .contact-role {
    font-weight: 300;
  }
  .contact-line {
    font-size: 15px;
    font-weight: 300;
    margin-top: 8px;
    color: var(--text-soft);
  }

  /* Back */
  .brand-back {
    position: absolute;
    left: 150px;
    top: 120px;
    color: var(--text-white);
    font-weight: 300;
    font-size: 50px;
    letter-spacing: 6px;
    line-height: 1.1;
    text-transform: uppercase;
  }
  .web-address {
    position: absolute;
    left: 152px;
    top: 268px;
    color: var(--text-soft);
    font-size: 18px;
    font-weight: 300;
    letter-spacing: 1px;
  }
</style>
</head>
<body>
<main class="sheet">

  <section class="card card-front" aria-label="Business card front">
    <svg class="card-art" viewBox="0 0 700 400" preserveAspectRatio="none" aria-hidden="true">
      <defs>
        <linearGradient id="frontBlue" x1="0" y1="0" x2="1" y2="1">
          <stop offset="0" stop-color="var(--blue-bright)"/>
          <stop offset="0.55" stop-color="var(--blue-mid)"/>
          <stop offset="1" stop-color="var(--blue-deep)"/>
        </linearGradient>
        <linearGradient id="frontEdge" x1="0" y1="0" x2="1" y2="0">
          <stop offset="0" stop-color="var(--blue-pale)"/>
          <stop offset="1" stop-color="var(--blue-light)"/>
        </linearGradient>
      </defs>
      <rect width="700" height="400" fill="url(#frontBlue)"/>
      <polygon points="0,0 700,0 700,58 280,306 0,258" fill="url(#frontEdge)"/>
      <polygon points="0,0 700,0 700,44 280,292 0,244" fill="var(--card-white)"/>
    </svg>

    <div class="brand-front">
      <span class="brand-mark" aria-hidden="true"></span>
      <span class="brand-name">Amber Loom<br>Systems</span>
    </div>

    <div class="contact">
      <p class="contact-name">Clara Fenwick <span class="contact-role">- Director</span></p>
      <p class="contact-line">0437 518 902</p>
      <p class="contact-line">clara.fenwick@amberLoomSystems.com.au</p>
    </div>
  </section>

  <section class="card card-back" aria-label="Business card back">
    <svg class="card-art" viewBox="0 0 700 400" preserveAspectRatio="none" aria-hidden="true">
      <defs>
        <linearGradient id="backBlue" x1="0" y1="0" x2="1" y2="1">
          <stop offset="0" stop-color="var(--blue-deep)"/>
          <stop offset="0.5" stop-color="var(--blue-mid)"/>
          <stop offset="1" stop-color="var(--blue-bright)"/>
        </linearGradient>
      </defs>
      <rect width="700" height="400" fill="url(#backBlue)"/>
      <polygon points="380,0 560,0 700,140 700,320" fill="var(--text-white)" opacity="0.06"/>
      <polygon points="0,300 300,400 0,400" fill="var(--blue-light)" opacity="0.18"/>
    </svg>

    <p class="brand-back">Amber Loom<br>Systems</p>
    <p class="web-address">amberLoomSystems.com.au</p>
  </section>

</main>
</body>
</html>
```